Medical Practice and Business Coaching Website Design

I need a professional website designed for a medical business, TQP Medical.
The website will be hosted on Vorluna (similar design functionality as ZEPT).

About the website:
Pages for the website:
- Home page (a brief overview of the company with a section for "Ultrasound Clinics" and "Coaching and Courses" that link to these pages with all the info and packages for these sections)
- About Us (section for company info and info about Delphine Ashcombe, founder and business coach)
- Ultrasound Clinics (all the info about ultrasound, our packages, links to book, gallery of 3D/4D images, FAQs, social media links)
- Coaching and Courses (All of our coaching package info, course info with a waiting list sign up, section for free business download resources, social media links, blog posts)
- Contact Us (info for our harrowgate ultrasound location and bookings with a map, contact form, email and phone details)

Pages that are also needed but not visible in the top menu:
- Blog Page
- Waiting List Page x2 (Kelloway pop-up 3D clinic, Online Course)
- Thanks for subscribing page

We have a company logo and a logo for both the ultrasound clinics and the Coaching sides of the business. They are attached as well as the HEX codes for the branding colours. Ideally the company areas of the site will be in the blue, purple and teal colours. The ultrasound clinics page will be mostly in the purple with the "clinics" logo featuring on the page.
The courses and coaching page will be dominant in the blue branding colours with accents of purple and teal. The courses logo will be somewhere on the page too.

About our company:
Our company has 2 separate businesses which will have their own pages on the website.
We have a medical imaging business which specialises in ultrasound. We have 3 locations/services:
- Harrowgate Ultrasound: open Fridays and the occasional saturday. Our main focus and where the focus on the clinical page needs to be.
- East Corrimbal Ultrasound: Currently closed, no re-opening date and unlikely to reopen.
- Pop-up clinics: most commonly occur in Kelloway. occasionally in Parkes. Dates for next pop-up will be announced in the future.

Our Harrowgate practice offers both diagnostic ultrasound (referral from doctor) for all areas of the body and 3d/4d pregnancy ultrasounds for entertainment purposes.
The content for the ultrasound clinics part of the website can be found on the current harrowgate ultrasound website: harrowgateultrasound.com.au
This website will be replaced by the new company site. All of the info on this site will end up on the clinics page of the new company website.

The second part of the company is a coaching and courses service for medical professionals who want to start or grow their business.
We currently have coaching packages for 1-on-1 online advice and guidance.

Coaching: all take place on Zoom and can be recorded for them to watch again after. Notes, documents and links that are discussed are provided after session

- FREE 15 minute session: discuss current business or business idea, if and how I can help and potential things they can do. One per client

- Single Coaching Session - 1hr with Delphine

- Silver coaching package: 1 x 1hr Coaching Call with Delphine
Unlimited Email with Delphine for 1 month
Access to our Private Facebook Group to network with other medical professionals and business owners

- Silver Coaching Package With Social Media Management:
As above with 1 month Social Media Management (15 posts, Facebook and Instagram)

- Gold coaching package: 2 x 1hr Coaching Calls with Delphine
Access to our Private Facebook

- Gold Coaching Package With Social Media Management:

- Business Sidekick Package: Unlimited Coaching Calls
Unlimited SMS
Unlimited Emails
Social Media Management (Facebook and Instagram, 1 post per day) Valued at over $700
Business Masterclass (something different each month...social media, medicare, website, branding, live events, etc)

Enrollment for our first course opens in May and clients can join the waitlist in the meantime.
Course is aimed at medical professionals who want to grow their patient numbers and create an online presence for their business.
Ideal for: small practices where the owner does everything, not necessarily familiar with marketing/social media/websites, goes to the very basics and steps through everything in getting a logo, branding, website, building social media pages, creating content.

Course name to come but it will be something like "helpful marketing in healthcare" or "the business of healthcare"

We will also have a blog on the website and a podcast (in the future).

I would like a testimonial on at least the clinics page and the coaching page. Here is one for each but I have more if need be:
Coaching: "I knew I wanted to start my own business but I had no idea where to begin. It would have been easy to abort my dreams of starting my own business had it not been for the direction and unwavering support of Delphine from TQP medical. Delphine dissected the process into manageable bit sized pieces for me and worked tirelessly behind the scenes ensuring everything was on track. Her friendly, warm and approachable manner
equated to more than her just being my business coach, she has now become a friend.
Thank you!!"

Ultrasound testimonial: "Amazing service! Best ultrasound experience I’ve had. Super friendly and informative staff. Great technology. If I didn’t live so far away I’d go to Harrowgate for all my ultrasounds!"

I would also like a section for a welcome video (yet to be recorded) on the home page, ultrasound clinics page and coaching/courses page.

I've attached the company logo and the sub-logos in different formats. There is also a head shot of Delphine for the about us page, an image of Delphine with a coaching client for the coaching page and multiple 3D ultrasound images for the gallery on the clinics page.

Target Market(s)

Mostly targeted at medical professionals. Pregnant women and anyone needing an ultrasound are the targets for the clinics page

Industry/Entity Type

Healthcare

Number of Pages Required

5+ page

Colors
0054AA
0677BA
7BADD7
CADEEF
E8F1F8
0094D4
00A9DD
6FCCEA
C7EBF8
E9F6FB
00AB8E
00BBA5
67D7C9
C6EFE9
E9F9F6
A7469A
B969AE
D3A5CF
EDDBEB
F8F0F9
6B429C
8869AF
B7A5CE
E3DAEB
F3F0F8

```html
<!DOCTYPE html>
<html lang="en">
<head>
<meta charset="utf-8">
<title>TQP Medical — Home</title>
<link href="https://fonts.googleapis.com/css2?family=Libre+Baskerville:wght@400;700&family=Tinos:ital,wght@0,400;0,700;1,400&family=Poppins:wght@400;500&display=swap" rel="stylesheet">
<style>
:root{
  --navy:#2b2f86;
  --blue:#0677ba;
  --sky:#0094d4;
  --teal:#00ab8e;
  --teal-2:#00bba5;
  --purple:#6b429c;
  --violet:#8869af;
  --magenta:#a7469a;
  --orchid:#b969ae;
  --ink:#1d1d2b;
  --grey:#8a8a94;
  --paper:#f5f5f6;
  --black:#050507;
  --white:#ffffff;
}
*{box-sizing:border-box;margin:0;padding:0}
html,body{width:1200px;height:4601px;overflow:hidden}
body{font-family:"Tinos",serif;color:var(--ink);background:var(--white);position:relative}
.section{position:absolute;left:0;width:1200px;overflow:hidden}
.heading{font-family:"Libre Baskerville",serif;font-weight:700;text-transform:uppercase;letter-spacing:-.5px}
.grad-text{background:linear-gradient(90deg,var(--purple),var(--navy) 45%,var(--teal));-webkit-background-clip:text;background-clip:text;color:transparent}

/* header */
.site-header{top:0;height:179px;background:var(--white)}
.topbar{position:absolute;left:150px;right:0;top:0;height:50px;background:linear-gradient(90deg,#d7d3ea 0%,var(--violet) 20%,var(--sky) 55%,var(--teal) 100%);clip-path:polygon(40px 0,100% 0,100% 100%,0 100%)}
.social{position:absolute;display:flex;gap:12px}
.social span{width:18px;height:18px;border-radius:50%;background:var(--white)}
.topbar .social{right:375px;top:16px}
.phone{position:absolute;right:110px;top:14px;color:var(--white);font-size:18px;display:flex;align-items:center;gap:8px}
.brand{position:absolute;left:155px;top:6px;width:110px;text-align:center}
.brand-mark{width:96px;height:96px;border-radius:50%;border:5px solid var(--purple);margin:0 auto;background:var(--white)}
.brand-name{font-size:20px;color:var(--purple);letter-spacing:2px;line-height:1;margin-top:4px}
.main-nav{position:absolute;left:338px;top:108px;display:flex;gap:38px;font-size:19px;color:var(--ink)}

/* hero */
.hero{top:179px;height:633px}
.hero-photo{position:absolute;inset:0;background:linear-gradient(100deg,#9aa0a6 0%,#c9cdd1 35%,#e7e8ea 60%,#b8bcc1 100%)}
.hero-shade{position:absolute;inset:0;background:linear-gradient(90deg,rgba(40,40,60,.55),rgba(40,40,60,.1) 60%,rgba(40,40,60,0))}
.hero-title{position:absolute;left:163px;top:212px;font-size:37px;line-height:48px;color:var(--white)}
.play{position:absolute;left:821px;top:269px;width:86px;height:86px;border-radius:50%;background:linear-gradient(135deg,var(--sky),var(--purple));border:4px solid var(--white)}
.play svg{position:absolute;left:29px;top:22px}
.hero-wave{position:absolute;left:0;bottom:0}

/* welcome */
.welcome{top:812px;height:470px;text-align:center}
.welcome h1{font-size:32px;margin-top:94px}
.lead{font-size:26px;line-height:35px;width:760px;margin:34px auto 0}
.body-copy{font-size:16.5px;line-height:23px;color:var(--grey);width:780px;margin:28px auto 0}

/* feature bands */
.band{color:var(--white)}
.band-clinics{top:1282px;height:588px;background:linear-gradient(90deg,#6f46a3,#8b4aa6 55%,#a0479c)}
.band-coaching{top:2406px;height:559px;background:linear-gradient(90deg,#0a7fc8,#3f5fb6 45%,#6b4aa4)}
.sub-logo{position:absolute;width:124px;height:124px;border-radius:50%;background:var(--white);display:flex;flex-direction:column;align-items:center;justify-content:center}
.sub-logo i{width:52px;height:52px;border-radius:50%;border:4px solid currentColor}
.sub-logo b{font-weight:400;font-size:15px;line-height:14px;margin-top:4px;letter-spacing:1px;text-align:center}
.band h2{position:absolute;font-size:32px;line-height:44px}
.band p{position:absolute;font-size:15.5px;line-height:18px;width:318px}
.btn{position:absolute;height:54px;border:2px solid var(--white);border-radius:27px;font-family:"Libre Baskerville",serif;font-weight:700;font-size:15px;color:var(--white);display:flex;align-items:center;justify-content:center}
.ring-photo{position:absolute;border-radius:50%}
.ring{position:absolute;border-radius:50%;border:2px solid rgba(255,255,255,.45)}

/* testimonials */
.testimonials{top:1870px;height:536px;background:var(--paper)}
.section-title{text-align:center;font-size:32px}
.testimonials .section-title{margin-top:100px}
.quote-card{position:absolute;top:218px;width:470px;height:190px}
.avatar{position:absolute;left:0;top:0;width:127px;height:127px;border-radius:50%;border:4px solid;background:linear-gradient(180deg,#d9d9d9,#a9a9a9)}
.quote-mark{position:absolute;left:122px;top:-6px;font-family:"Libre Baskerville",serif;font-size:60px;color:#d5d5d8;line-height:1}
.quote{position:absolute;left:160px;top:8px;width:250px;font-style:italic;font-size:13px;line-height:19px;color:var(--grey)}
.cite{position:absolute;left:160px;top:178px;font-size:13px;line-height:18px}
.cite b{font-family:"Libre Baskerville",serif;display:block}
.cite span{color:var(--grey);letter-spacing:1px}
.divider-v{position:absolute;left:600px;top:230px;width:1px;height:170px;background:#dedee3}
.dots{position:absolute;top:460px;left:0;width:1200px;display:flex;justify-content:center;gap:4px}
.dots span{width:14px;height:14px;border-radius:50%;background:#dcdce2}
.dots span:first-child{background:linear-gradient(135deg,var(--purple),var(--blue))}

/* blog */
.blog{top:2965px;height:776px;background:var(--paper)}
.blog .section-title{margin-top:130px;font-size:44px;background:linear-gradient(90deg,var(--navy) 40%,var(--teal));-webkit-background-clip:text;background-clip:text;color:transparent}
.post{position:absolute;top:230px;width:300px;text-align:center}
.post-photo{width:258px;height:258px;border-radius:50%;margin:0 auto;border:6px solid}
.post h3{font-family:"Libre Baskerville",serif;font-size:14px;line-height:20px;margin-top:56px;color:var(--ink)}
.post p{font-size:14px;line-height:17px;color:var(--grey);margin-top:10px}
.post time{display:block;font-family:"Poppins",sans-serif;font-size:13px;color:var(--navy);margin-top:16px}
.post time::before{content:"";display:inline-block;width:9px;height:10px;background:var(--purple);margin-right:5px;vertical-align:-1px}

/* brand strip & footer */
.brands{top:3741px;height:860px;background:var(--white)}
.footer-wave{position:absolute;left:0;top:0}
.brand-item{position:absolute;top:110px;transform:translateX(-50%);text-align:center;font-size:26px;line-height:22px;letter-spacing:2px;white-space:nowrap}
.brand-item i{display:block;width:104px;height:104px;border-radius:50%;border:5px solid currentColor;margin:0 auto 6px;background:var(--white)}
.brand-item small{display:block;font-size:18px;letter-spacing:1.5px}
.footer-logo{position:absolute;left:148px;top:537px;text-align:center}
.footer-logo i{display:block;width:118px;height:118px;border-radius:50%;border:5px solid var(--violet);margin:0 auto}
.footer-logo span{display:block;font-size:26px;line-height:24px;color:var(--violet);letter-spacing:2px;margin-top:10px}
.footer-col{position:absolute;top:550px;color:var(--white);font-size:15px;line-height:29px}
.footer-col ul{list-style:none}
.footer-col .sub{font-size:13px;line-height:22px;color:#8a8aa0;padding-left:20px}
.footer-col .sub li::before{content:"";display:inline-block;width:5px;height:5px;border-radius:50%;background:var(--violet);margin-right:8px;vertical-align:2px}
.footer-col h4{font-weight:400;font-size:19px}
.email-field{width:225px;border-bottom:2px solid #c8c8d2;font-size:14px;color:#c8c8d2;padding-bottom:4px;margin-top:10px}
.signup{margin-top:26px;width:112px;height:42px;border-radius:21px;background:linear-gradient(90deg,var(--blue),var(--purple));font-family:"Poppins",sans-serif;font-size:13px;display:flex;align-items:center;justify-content:center;letter-spacing:1px}
.footer-rule{position:absolute;left:145px;width:918px;top:745px;height:1px;background:#3a3a48}
.brands .social{left:170px;top:793px;gap:12px}
.brands .social span{width:20px;height:20px}
.copyright{position:absolute;right:152px;top:795px;color:var(--white);font-size:12.5px}
</style>
</head>
<body>

<header class="section site-header">
  <div class="topbar">
    <div class="social" aria-label="Social links"><span></span><span></span><span></span><span></span><span></span></div>
    <div class="phone">
      <svg width="16" height="16" viewBox="0 0 24 24" fill="#fff"><path d="M6.6 10.8a15.1 15.1 0 0 0 6.6 6.6l2.2-2.2c.3-.3.7-.4 1-.2 1.1.4 2.3.6 3.6.6.6 0 1 .4 1 1V20c0 .6-.4 1-1 1A17 17 0 0 1 3 4c0-.6.4-1 1-1h3.5c.6 0 1 .4 1 1 0 1.3.2 2.5.6 3.6.1.3 0 .7-.2 1z"/></svg>
      Call Us: 555 010 4477
    </div>
  </div>
  <div class="brand">
    <div class="brand-mark"></div>
    <div class="brand-name">TQP<br>MEDICAL</div>
  </div>
  <nav class="main-nav">
    <span>Home</span><span>About Us</span><span>Ultrasound Clinics</span><span>Coaching and Courses</span><span>Contact Us</span>
  </nav>
</header>

<section class="section hero">
  <div class="hero-photo" role="img" aria-label="Sonographer performing an ultrasound scan on a patient, monitor in the background"></div>
  <div class="hero-shade"></div>
  <h2 class="heading hero-title">TQP Medical is<br>one of the biggest<br>ultrasound<br>clinics practice</h2>
  <div class="play" aria-label="Play welcome video"><svg width="34" height="38" viewBox="0 0 34 38"><path d="M2 2 L32 19 L2 36Z" fill="#fff"/></svg></div>
  <svg class="hero-wave" width="1200" height="120" viewBox="0 0 1200 120"><path d="M0 78 Q600 180 1200 40 L1200 120 L0 120Z" fill="#fff"/></svg>
</section>

<section class="section welcome">
  <h1 class="heading grad-text">Welcome to TQP Medical</h1>
  <p class="lead">Lorem ipsum dolor sit amet, consectetur adipiscing elit, sed do eiusmod tempor incididunt ut labore magna aliqua.</p>
  <p class="body-copy">Lorem ipsum dolor sit amet, consectetur adipiscing elit, sed do eiusmod tempor incididunt ut labore et dolore magna aliqua. Quis ipsum suspendisse ultrices gravida. Risus commodo viverra maecenas accumsan lacus vel facilisis. Lorem ipsum dolor sit amet, consectetur adipiscing elit, sed do eiusmod tempor incididunt ut labore et dolore magna aliqua. Quis ipsum suspendisse ultrices gravida. Risus commodo viverra maecenas accumsan lacus vel facilisis.</p>
</section>

<section class="section band band-clinics">
  <div class="sub-logo" style="left:149px;top:124px;color:var(--magenta)"><i></i><b>TQP<br>CLINICS</b></div>
  <h2 class="heading" style="left:296px;top:136px">Ultrasound<br>Clinics</h2>
  <p style="left:296px;top:240px">Lorem ipsum dolor sit amet, consectetur adipiscing elit, sed do eiusmod tempor incididunt ut lablorore et dolore magna ali qua uis ipsum suspendisse uloreltrices avida sus commodo viverloyra maecenas accusan lacus vel facilisis. Lorem ipsum dolor sit aet, consectetur adipiscing elit, sed do eiusmod tempor incididunt ut labore et dolore magna aliquacommodo viverra maecenas accsan la cus vel facilisis.</p>
  <div class="btn" style="left:296px;top:446px;width:148px">READ MORE</div>
  <div class="ring" style="left:690px;top:115px;width:410px;height:410px"></div>
  <div class="ring" style="left:708px;top:133px;width:374px;height:374px;border-color:rgba(255,255,255,.3)"></div>
  <div class="ring-photo" style="left:727px;top:152px;width:336px;height:336px;background:linear-gradient(135deg,#e9e6e6,#c9b7ae 50%,#8b7f7a)" role="img" aria-label="Two clinic staff members standing beside an ultrasound machine"></div>
</section>

<section class="section testimonials">
  <h2 class="heading grad-text section-title">Client Testimonials</h2>
  <div class="quote-card" style="left:151px">
    <div class="avatar" style="border-color:var(--teal)" role="img" aria-label="Client portrait"></div>
    <span class="quote-mark">“</span>
    <p class="quote">Lorem ipsum dolor sit amet, consectetur adipiscing elit, sed do eiusmod tempor incididunt ut lablorore et dolore magna ali q uauis ipsum suspendisse ultrices gra vidaisus commodo viverra maecenas accumsan lacus vel facilisiorem ipsum dolor sit amet, consectetur</p>
    <div class="cite"><b style="color:var(--teal)">MOREN TAVI,</b><span>CITY NAME</span></div>
  </div>
  <div class="divider-v"></div>
  <div class="quote-card" style="left:633px">
    <div class="avatar" style="border-color:var(--purple)" role="img" aria-label="Client portrait"></div>
    <span class="quote-mark">“</span>
    <p class="quote">Lorem ipsum dolor sit amet, consectetur adipiscing elit, sed do eiusmod tempor incididunt ut lablorore et dolore magna ali q uauis ipsum suspendisse ultrices gra vidaisus commodo viverra maecenas accumsan lacus vel facilisiorem ipsum dolor sit amet, consectetur</p>
    <div class="cite"><b style="color:var(--purple)">MOREN TAVI,</b><span>CITY NAME</span></div>
  </div>
  <div class="dots"><span></span><span></span><span></span><span></span><span></span><span></span><span></span><span></span></div>
</section>

<section class="section band band-coaching">
  <div class="ring" style="left:152px;top:104px;width:410px;height:410px;border:4px solid #5fb3f0"></div>
  <div class="ring" style="left:166px;top:118px;width:382px;height:382px;border:2px solid #4aa3ea"></div>
  <div class="ring-photo" style="left:187px;top:139px;width:340px;height:340px;background:radial-gradient(circle at 45% 45%,#e8b889 0%,#b9784c 40%,#2a1a12 75%,#0d0a08)" role="img" aria-label="3D ultrasound image of a baby"></div>
  <div class="sub-logo" style="left:592px;top:124px;color:var(--blue)"><i></i><b>TQP<br>COURSES</b></div>
  <h2 class="heading" style="left:732px;top:126px">Coaching<br>and Courses</h2>
  <p style="left:732px;top:232px">Lorem ipsum dolor sit amet, consectetur adipiscing elit, sed do eiusmod tempor incididunt ut lablorore et dolore magna ali qua uis ipsum suspendisse uloreltrices avida sus commodo viverloyra maecenas accusan lacus vel facilisis. Lorem ipsum dolor sit aet, consectetur adipiscing elit, sed do eiusmod tempor incididunt ut labore et dolore magna aliquacommodo viverra maecenas accsan la cus vel facilisis.</p>
  <div class="btn" style="left:734px;top:437px;width:148px">READ MORE</div>
</section>

<section class="section blog">
  <h2 class="heading section-title">Latest Blog Posts</h2>
  <article class="post" style="left:141px">
    <div class="post-photo" style="border-color:var(--purple);background:linear-gradient(135deg,#d9d9df,#a9adb8)" role="img" aria-label="Pregnant patient resting on a clinic bed"></div>
    <h3>LOREM IPSUM DOLOR SIT AM<br>CONS ECTETUR ASCING</h3>
    <p>Lorem ipsum dolor sit amet, consec tet ur adipiscing elit, sed do eiusmod tem por incididunt ut lablorvel facilisis.</p>
    <time>March 18</time>
  </article>
  <article class="post" style="left:450px">
    <div class="post-photo" style="border-color:var(--teal);background:linear-gradient(135deg,#e6eef6,#7aa7d4)" role="img" aria-label="Ultrasound probe being used during a scan"></div>
    <h3>LOREM IPSUM DOLOR SIT AM<br>CONS ECTETUR ASCING</h3>
    <p>Lorem ipsum dolor sit amet, consec tet ur adipiscing elit, sed do eiusmod tem por incididunt ut lablorvel facilisis.</p>
    <time>March 18</time>
  </article>
  <article class="post" style="left:768px">
    <div class="post-photo" style="border-color:var(--navy);background:linear-gradient(135deg,#f1e3d8,#c9a48c)" role="img" aria-label="Hands holding an ultrasound print over a pregnant belly"></div>
    <h3>LOREM IPSUM DOLOR SIT AM<br>CONS ECTETUR ASCING</h3>
    <p>Lorem ipsum dolor sit amet, consec tet ur adipiscing elit, sed do eiusmod tem por incididunt ut lablorvel facilisis.</p>
    <time>March 18</time>
  </article>
</section>

<footer class="section brands">
  <svg class="footer-wave" width="1200" height="860" viewBox="0 0 1200 860">
    <defs><linearGradient id="edge" x1="0" x2="1"><stop offset="0" stop-color="#6b429c"/><stop offset=".5" stop-color="#0677ba"/><stop offset="1" stop-color="#00ab8e"/></linearGradient></defs>
    <path d="M0 555 C180 420 420 500 640 505 C880 510 1060 420 1200 195 L1200 860 L0 860Z" fill="url(#edge)"/>
    <path d="M0 572 C180 440 420 520 640 525 C880 530 1060 440 1200 225 L1200 860 L0 860Z" fill="#050507"/>
  </svg>
  <div class="brand-item" style="left:229px;color:var(--magenta)"><i></i>TQP<small>CLINICS</small></div>
  <div class="brand-item" style="left:384px;color:var(--blue)"><i></i>TQP<small>COURSES</small></div>
  <div class="brand-item" style="left:563px;color:var(--navy)"><i></i>TQP<small>EDUCATION</small></div>
  <div class="brand-item" style="left:741px;color:var(--teal)"><i></i>TQP<small>MARKETPLACE</small></div>
  <div class="brand-item" style="left:952px;color:var(--teal)"><i></i>TQP<small>MEDICAL EQUIPMENT</small></div>

  <div class="footer-logo"><i></i><span>TQP<br>MEDICAL</span></div>
  <div class="footer-col" style="left:357px">
    <ul><li>Home</li><li>About Us</li><li>Ultrasound Clinics</li><li>Coaching and Courses</li><li>Contact Us</li></ul>
  </div>
  <div class="footer-col" style="left:589px">
    <ul><li>Waiting List</li></ul>
    <ul class="sub"><li>Kelloway pop-up 3D clinic</li><li>Online Course</li></ul>
    <ul><li>Blog page</li></ul>
  </div>
  <div class="footer-col" style="left:825px">
    <h4>Subscribe Newsletter</h4>
    <div class="email-field">Email</div>
    <div class="signup">SIGN UP</div>
  </div>
  <div class="footer-rule"></div>
  <div class="social" aria-label="Social links"><span></span><span></span><span></span><span></span><span></span></div>
  <div class="copyright">Copyrights © 2022 All Rights Reserved</div>
</footer>

</body>
</html>
```